business card for a massage therapy practice named 'Cedar and Willow Massage Studio'

I really need a trendy, yet easy on the eyes business card to complement my logo. Ideally with some gold or rose gold foil work.

My uploaded file of the logo I have in horizontal but I have a vertical version as well. Another color that is used in the website is a blush pink here and there. I'd like to see some trendy tropical leaves in the design.

```html
<!DOCTYPE html>
<html lang="en">
<head>
<meta charset="utf-8">
<title>Cedar and Willow Massage Studio – Business Card</title>
<link href="https://fonts.googleapis.com/css2?family=Arimo:wght@400&display=swap" rel="stylesheet">
<style>
  :root {
    --backdrop: #2b2b2d;
    --card: #121212;
    --foil: #c8a47c;
    --foil-soft: #b8966f;
  }
  html, body {
    margin: 0;
    padding: 0;
    overflow: hidden;
  }
  body {
    width: 1200px;
    height: 1017px;
    background: var(--backdrop);
    font-family: "Arimo", Arial, sans-serif;
    position: relative;
  }
  .card {
    position: absolute;
    width: 490px;
    height: 280px;
    background: var(--card);
    border-radius: 3px;
    box-shadow: 0 18px 40px rgba(0,0,0,0.45);
    color: var(--foil);
  }
  .card-front { left: 90px; top: 200px; }
  .card-back  { left: 620px; top: 530px; }

  /* Front: brand name */
  .brand {
    position: absolute;
    left: 0; right: 0; top: 0; bottom: 0;
    display: flex;
    align-items: center;
    justify-content: center;
    gap: 14px;
  }
  .brand-dot {
    width: 14px;
    height: 14px;
    border-radius: 50%;
    background: var(--foil);
  }
  .brand-name {
    font-size: 22px;
    letter-spacing: 0.5px;
    line-height: 1.35;
    color: var(--foil);
  }
  .brand-name span { display: block; }

  /* Back: person + contact */
  .person {
    position: absolute;
    right: 262px;
    top: 112px;
    text-align: right;
  }
  .person-name {
    font-size: 20px;
    line-height: 1.2;
  }
  .person-role {
    font-size: 14px;
    line-height: 1.3;
  }
  .divider {
    position: absolute;
    left: 245px;
    top: 70px;
    width: 1px;
    height: 110px;
    background: var(--foil-soft);
  }
  .contact {
    position: absolute;
    left: 260px;
    top: 76px;
    font-size: 12.5px;
    line-height: 1.45;
  }
  .contact p { margin: 0; }
  .contact .group + .group { margin-top: 8px; }
</style>
</head>
<body>
  <section class="card card-front" aria-label="Card front">
    <div class="brand">
      <div class="brand-dot"></div>
      <div class="brand-name">
        <span>Cedar &amp; Willow</span>
        <span>Massage Studio</span>
      </div>
    </div>
  </section>

  <section class="card card-back" aria-label="Card back">
    <div class="person">
      <div class="person-name">Marisol Vega</div>
      <div class="person-role">Massage Therapist</div>
    </div>
    <div class="divider"></div>
    <div class="contact">
      <div class="group">
        <p>482 Elm Ave #210</p>
        <p>Fairview, CA 95000</p>
      </div>
      <div class="group">
        <p>(555) 204-7731</p>
        <p>info@cedarandwillow.com</p>
        <p>www.cedarandwillow.com</p>
      </div>
    </div>
  </section>
</body>
</html>
```